Pool Screen Enclosure Building a Career Boot Camp!

Looking to Host a Boot Camp for people looking for a career or looking to change careers. We Design, Manufacture and Install Custom Pool Screen Enclosures. We have a training program to allow Non Experienced motivated people the chance at a great career that will provide a great living for them and their family. This will be a paid boot camp, week long, we provide all the initial training for them to make a transition into our business. This will be 5 days of training with a guaranteed job to start the following Monday.... This is good for both someone with no construction experience or someone with construction experience that wants to upgrade their current job.
Paid Boot Camp
transition to a full time job with great pay
Benefits include Health Insurance, Dental and Vision, 401K, we provide the tools and training.

```html
<!DOCTYPE html>
<html lang="en">
<head>
<meta charset="UTF-8">
<title>Paid Boot Camp Flyer</title>
<link href="https://fonts.googleapis.com/css2?family=Oswald:wght@700&family=Montserrat:wght@400;600;700;800&display=swap" rel="stylesheet">
<style>
  :root{
    --green:#1a7a2a;
    --yellow:#ffe600;
    --black:#0a0a0a;
    --white:#ffffff;
    --ink:#1b1b1b;
    --page-bg:#e9e9e9;
  }
  *{box-sizing:border-box;margin:0;padding:0}
  html,body{width:1200px;height:800px;overflow:hidden;background:var(--page-bg)}
  body{display:flex;align-items:center;justify-content:center;font-family:"Montserrat",sans-serif;color:var(--ink)}
  .flyer{position:relative;width:600px;height:776px;background:var(--white);overflow:hidden;box-shadow:0 4px 18px rgba(0,0,0,.18)}
  .hero-photo{position:absolute;left:0;top:0;width:600px;height:330px;background:linear-gradient(160deg,#d8d2d6 0%,#a9a3a8 35%,#5f7f6a 62%,#5f9aa0 78%,#c9b79c 100%)}
  .title-band{position:absolute;left:0;top:305px;width:378px;height:58px;background:var(--green);clip-path:polygon(0 0,100% 0,95% 100%,0 100%);display:flex;align-items:center;padding-left:20px}
  .title-band h1{font-family:"Oswald",sans-serif;font-weight:700;font-size:38px;color:var(--white);letter-spacing:.5px;line-height:1;white-space:nowrap}
  .gallery{position:absolute;left:380px;top:250px;width:220px;height:382px;background:var(--yellow);padding:8px 8px 8px 10px;display:flex;flex-direction:column;gap:7px}
  .gallery-photo{flex:1}
  .gallery-photo.roof{background:linear-gradient(150deg,#8fb4d8,#dfe7ee 55%,#7d8a93)}
  .gallery-photo.frame{background:linear-gradient(160deg,#b7cde0,#eef2f5 50%,#6d8a5c)}
  .gallery-photo.crew{background:linear-gradient(150deg,#e6e1d6,#c9b9a3 55%,#8a6a5a)}
  .intro{position:absolute;left:22px;top:371px;width:345px;font-weight:800;font-size:11.5px;line-height:1.3}
  .services-head{position:absolute;left:18px;top:410px;width:352px;height:22px;border-top:2px solid var(--green)}
  .services-tag{position:absolute;left:0;top:-1px;background:var(--green);color:var(--yellow);font-weight:800;font-size:12px;padding:3px 18px 3px 8px;clip-path:polygon(0 0,100% 0,88% 100%,0 100%)}
  .services-list{position:absolute;left:22px;top:437px;width:345px;list-style:none;font-size:9.3px;line-height:1.3}
  .services-list li{display:flex;gap:6px;margin-bottom:4px}
  .services-list svg{flex:none;margin-top:1px}
  .details-card{position:absolute;left:16px;top:540px;width:354px;height:158px;background:var(--green);border-radius:12px;color:var(--white);padding:9px 12px;font-size:8.8px;line-height:1.3}
  .details-card p{margin-bottom:4px}
  .details-card em{font-style:normal;color:var(--yellow);font-weight:700}
  .benefits-rule{border-top:1px solid rgba(255,255,255,.5);margin:5px 0 4px}
  .benefits-head{color:var(--yellow);font-weight:800;font-size:12px;margin-bottom:4px}
  .benefits{display:grid;grid-template-columns:1.4fr .7fr 1fr;gap:5px 8px;list-style:none}
  .benefits li{display:flex;align-items:center;gap:5px;font-size:8.3px;line-height:1.2}
  .benefits svg{flex:none}
  .footer{position:absolute;left:0;top:704px;width:600px;height:72px;background:var(--black)}
  .brand{position:absolute;left:36px;top:726px;display:flex;align-items:center;gap:10px;font-weight:800;font-size:22px;color:var(--green)}
  .brand-dot{width:22px;height:22px;border-radius:50%;background:var(--yellow)}
  .contact{position:absolute;left:374px;top:632px;width:226px;height:72px;background:var(--green);border-bottom-left-radius:14px;color:var(--white);font-size:8.2px;font-style:normal;padding:6px 10px;display:flex;flex-direction:column;justify-content:center;gap:3px}
  .contact span{display:flex;align-items:center;gap:5px;white-space:nowrap}
</style>
</head>
<body>
<main class="flyer">
  <div class="hero-photo" role="img" aria-label="Screened pool enclosure overlooking a lake"></div>

  <div class="title-band"><h1>PAID BOOT CAMP</h1></div>

  <section class="gallery">
    <div class="gallery-photo roof" role="img" aria-label="Installers fitting a screen roof panel"></div>
    <div class="gallery-photo frame" role="img" aria-label="Worker on an enclosure frame under construction"></div>
    <div class="gallery-photo crew" role="img" aria-label="Trainees reviewing plans on site"></div>
  </section>

  <p class="intro">Looking to Host a Boot Camp for people looking for a career or looking to change careers.</p>

  <div class="services-head"><span class="services-tag">OUR SERVICES</span></div>
  <ul class="services-list">
    <li><svg width="10" height="10" viewBox="0 0 10 10"><circle cx="5" cy="5" r="5" fill="#1a7a2a"/><path d="M2.6 5.2l1.6 1.5 3.2-3.3" stroke="#fff" stroke-width="1.3" fill="none"/></svg>We Design, Manufacture and Install Custom Pool Screen Enclosures.</li>
    <li><svg width="10" height="10" viewBox="0 0 10 10"><circle cx="5" cy="5" r="5" fill="#1a7a2a"/><path d="M2.6 5.2l1.6 1.5 3.2-3.3" stroke="#fff" stroke-width="1.3" fill="none"/></svg>This will be a paid boot camp, week long, we provide all the initial training for them to make a transition into our business.</li>
    <li><svg width="10" height="10" viewBox="0 0 10 10"><circle cx="5" cy="5" r="5" fill="#1a7a2a"/><path d="M2.6 5.2l1.6 1.5 3.2-3.3" stroke="#fff" stroke-width="1.3" fill="none"/></svg>We have a training program to allow Non Experienced motivated people the chance at a great career that will provide a great living for them and their family.</li>
  </ul>

  <section class="details-card">
    <p>This will be <em>5 DAYS</em> of training with a <em>GUARANTEED JOB</em> to start the following <em>MONDAY</em>....</p>
    <p>This is good for both someone with no construction experience or someone with construction experience that wants to upgrade their current job.</p>
    <div class="benefits-rule"></div>
    <h2 class="benefits-head">BENEFITS</h2>
    <ul class="benefits">
      <li><svg width="14" height="14" viewBox="0 0 14 14"><circle cx="7" cy="7" r="5.5" fill="none" stroke="#ffe600" stroke-width="1.4"/><path d="M7 4v6M5 5.5h3.5M5 8.5h3.5" stroke="#fff" stroke-width="1"/></svg>Transition to a full time job with great pay</li>
      <li><svg width="14" height="14" viewBox="0 0 14 14"><ellipse cx="7" cy="8" rx="5.5" ry="4.5" fill="none" stroke="#ffe600" stroke-width="1.4"/><path d="M7 5.5v5" stroke="#fff" stroke-width="1"/></svg>401K</li>
      <li><svg width="14" height="14" viewBox="0 0 14 14"><rect x="1.5" y="2" width="11" height="8" fill="none" stroke="#ffe600" stroke-width="1.4"/><path d="M5 12h4" stroke="#fff" stroke-width="1.2"/></svg>we provide the tools &amp; training.</li>
      <li><svg width="14" height="14" viewBox="0 0 14 14"><rect x="2" y="1.5" width="10" height="11" rx="1" fill="none" stroke="#ffe600" stroke-width="1.4"/><path d="M7 4.5v5M4.5 7h5" stroke="#fff" stroke-width="1.2"/></svg>Health Insurance</li>
      <li></li>
      <li><svg width="14" height="14" viewBox="0 0 14 14"><path d="M3 2.5c2-1 6-1 8 0 .5 3-1 9-2 9s-1-4-2-4-1 4-2 4-2.5-6-2-9z" fill="none" stroke="#ffe600" stroke-width="1.3"/></svg>Dental and Vision</li>
    </ul>
  </section>

  <div class="footer"></div>
  <div class="brand"><span class="brand-dot"></span>Harbor Screen Works</div>

  <address class="contact">
    <span><svg width="9" height="9" viewBox="0 0 10 10"><path d="M5 1a3 3 0 0 1 3 3c0 2-3 5.5-3 5.5S2 6 2 4a3 3 0 0 1 3-3z" fill="#fff"/></svg>1180 Palm Grove Road, Sunport FL 30412</span>
    <span><svg width="9" height="9" viewBox="0 0 10 10"><path d="M2 1l2 .5.5 2-1 1a6 6 0 0 0 2 2l1-1 2 .5.5 2C5 9 1 5 2 1z" fill="#fff"/></svg>555-014-2290</span>
    <span><svg width="9" height="9" viewBox="0 0 10 10"><rect x="1" y="2.5" width="8" height="5.5" fill="none" stroke="#fff"/><path d="M1 2.5l4 3 4-3" stroke="#fff" fill="none"/></svg>info@harborscreenworks.com</span>
    <span><svg width="9" height="9" viewBox="0 0 10 10"><circle cx="5" cy="5" r="4" fill="none" stroke="#fff"/><path d="M1 5h8M5 1c2 2 2 6 0 8M5 1c-2 2-2 6 0 8" stroke="#fff" fill="none" stroke-width=".7"/></svg>www.harborscreenworks.com</span>
  </address>
</main>
</body>
</html>
```